Request for Business Card Design

Hi. My name is Marlene, I am looking for a new business card design for my company, Quarrow Signal Instruments, LLC. I really like the design you did for Tarsel Venture and was hoping you could do something similar using our full logo and our mark. I am also open to any raised texture design using our mark. I have attached our full logo, which would need to be somewhere on the card, as well as the mark in both outline and full form, as well as our brand colors / guide. The card does not have to be white, as long as our logo and mark appear. I actually like darker colored business cards more, but am open to all options. If you are interested in working with me, please let me know. We would also take the business card design into letterhead design if you can do that.

```html
<!DOCTYPE html>
<html lang="en">
<head>
<meta charset="utf-8">
<title>Quarrow Signal Instruments – Business Card</title>
<link href="https://fonts.googleapis.com/css2?family=Saira:wght@700&family=Arimo:ital,wght@0,400;0,700;1,400&display=swap" rel="stylesheet">
<style>
  :root {
    --page-bg: #121212;
    --card-bg: #222222;
    --accent: #0f8fb8;
    --ink: #f2f2f2;
    --ink-soft: #d9d9d9;
    --ghost: #1f2c32;
    --rule: #cfcfcf;
  }
  * { margin: 0; padding: 0; box-sizing: border-box; }
  html, body {
    width: 1200px; height: 963px; overflow: hidden;
    background: var(--page-bg);
  }
  .stage {
    width: 1200px; height: 963px;
    display: flex; flex-direction: column; align-items: center; justify-content: center;
    gap: 44px;
  }
  .card {
    position: relative;
    width: 720px; height: 412px;
    background: var(--card-bg);
    border-radius: 22px;
    border-bottom: 4px solid var(--accent);
    overflow: hidden;
  }

  /* Front */
  .brand {
    position: absolute; left: 56px; top: 150px;
    display: flex; align-items: center; gap: 16px;
    font-family: "Saira", sans-serif; font-weight: 700; color: var(--ink);
  }
  .brand-dot {
    width: 46px; height: 46px; border-radius: 50%;
    background: var(--accent);
    flex: none;
  }
  .brand-name { font-size: 40px; line-height: 1; letter-spacing: 4px; }
  .brand-tagline { font-size: 12.5px; line-height: 1; letter-spacing: 1.6px; margin-top: 6px; }

  .divider {
    position: absolute; left: 372px; top: 96px;
    width: 1px; height: 220px; background: var(--rule);
  }
  .contact {
    position: absolute; left: 402px; top: 104px;
    font-family: "Arimo", sans-serif; color: var(--ink-soft);
  }
  .person-name {
    font-weight: 700; font-size: 22px; letter-spacing: 1px;
    color: var(--accent); text-transform: uppercase;
  }
  .person-role { font-size: 17px; margin-top: 2px; }
  .address { font-size: 17px; line-height: 1.3; margin-top: 18px; }
  .contact-list { list-style: none; margin-top: 14px; }
  .contact-list li {
    display: flex; align-items: center; gap: 12px;
    font-size: 17px; line-height: 1.65;
  }
  .contact-list svg { width: 16px; height: 16px; flex: none; }

  /* Back */
  .back-mark {
    position: absolute; left: 250px; top: 40px;
    width: 360px; height: 360px; border-radius: 50%;
    border: 56px solid var(--ghost);
  }
  .back-brand {
    position: absolute; left: 0; right: 0; top: 150px;
    text-align: center;
    font-family: "Saira", sans-serif; font-weight: 700; color: var(--ink);
  }
  .back-brand .brand-name { font-size: 80px; letter-spacing: 8px; }
  .back-brand .brand-tagline { font-size: 22px; letter-spacing: 3px; margin-top: 8px; }
</style>
</head>
<body>
<main class="stage">

  <section class="card card-front" aria-label="Business card front">
    <div class="brand">
      <span class="brand-dot"></span>
      <div>
        <div class="brand-name">QUARROW</div>
        <div class="brand-tagline">SIGNAL INSTRUMENTS</div>
      </div>
    </div>

    <div class="divider"></div>

    <div class="contact">
      <p class="person-name">Elias Brandt</p>
      <p class="person-role">Manager</p>
      <p class="address">Your Address, City<br>State, Zip 0000</p>
      <ul class="contact-list">
        <li>
          <svg viewBox="0 0 24 24" fill="var(--accent)" aria-hidden="true"><path d="M6.6 10.8a15.1 15.1 0 0 0 6.6 6.6l2.2-2.2c.3-.3.7-.4 1-.2 1.1.4 2.3.6 3.6.6.6 0 1 .4 1 1V20c0 .6-.4 1-1 1A17 17 0 0 1 3 4c0-.6.4-1 1-1h3.5c.6 0 1 .4 1 1 0 1.3.2 2.5.6 3.6.1.3 0 .7-.2 1z"/></svg>
          123-456-2100
        </li>
        <li>
          <svg viewBox="0 0 24 24" fill="none" stroke="var(--accent)" stroke-width="2" aria-hidden="true"><rect x="3" y="5" width="18" height="14" rx="1"/><path d="M3 6l9 7 9-7"/></svg>
          youremail@mailbox.com
        </li>
        <li>
          <svg viewBox="0 0 24 24" fill="none" stroke="var(--accent)" stroke-width="2" aria-hidden="true"><circle cx="12" cy="12" r="9"/><path d="M3 12h18M12 3c3 3 3 15 0 18M12 3c-3 3-3 15 0 18"/></svg>
          www.yourwebsite.com
        </li>
      </ul>
    </div>
  </section>

  <section class="card card-back" aria-label="Business card back">
    <div class="back-mark"></div>
    <div class="back-brand">
      <div class="brand-name">QUARROW</div>
      <div class="brand-tagline">SIGNAL INSTRUMENTS</div>
    </div>
  </section>

</main>
</body>
</html>
```